Bramlow Building

We are a General building contractor who specialises in building extensions, loft conversions, basement conversions, and general property refurbishment. The design should promote our company strap line On time-On budget-guaranteed. The design should also promote a confident and secure feeling as negotiating or contacting a builder can be a daunting task for most people who have not had any previous work. We have 30yrs experience within the industry. We intend to promote a VAT free offer.

```html
<!DOCTYPE html>
<html lang="en">
<head>
<meta charset="utf-8">
<title>Bramlow Building – VAT Free Offer</title>
<link href="https://fonts.googleapis.com/css2?family=Crimson+Pro:wght@400;500;600;700&family=Oswald:wght@600&display=swap" rel="stylesheet">
<style>
  :root {
    --paper: #ffffff;
    --ink: #333333;
    --ink-soft: #8a8a8a;
    --navy: #1f2c5c;
    --band: #4d8fc6;
    --offer-red: #e1242b;
    --label-red: #d8262d;
  }
  * { box-sizing: border-box; margin: 0; padding: 0; }
  html, body { width: 1200px; height: 851px; overflow: hidden; background: var(--paper); }
  .flyer { position: relative; width: 1200px; height: 851px; background: var(--paper); font-family: "Crimson Pro", Georgia, serif; overflow: hidden; }

  .brand { position: absolute; right: 887px; top: 40px; text-align: right; color: var(--navy); }
  .brand-name { font-size: 28px; font-weight: 700; line-height: 1; letter-spacing: 0.2px; }

  .intro { position: absolute; right: 887px; top: 126px; text-align: right; }
  .intro-lead { color: var(--ink-soft); font-size: 22px; line-height: 28px; margin-bottom: 37px; }
  .intro-services { color: var(--ink); font-size: 21.5px; font-weight: 500; line-height: 29.5px; }

  .strapline { position: absolute; right: 887px; top: 478px; text-align: right; color: var(--band); font-size: 22px; font-weight: 600; line-height: 28px; }

  .photo { position: absolute; }
  .photo-apartments { left: 355px; top: 40px; width: 398px; height: 304px; background: linear-gradient(165deg, #d9d6cf 0%, #cfb3a6 55%, #c8b7ab 100%); }
  .photo-house { left: 757px; top: 40px; width: 403px; height: 304px; background: linear-gradient(175deg, #dcdedf 0%, #d6d4cf 55%, #c4bab2 100%); }
  .photo-floor { left: 355px; top: 348px; width: 265px; height: 360px; background: linear-gradient(165deg, #c8ccd1 0%, #ccd8e4 55%, #b8c6d8 100%); }
  .photo-footings-a { left: 624px; top: 348px; width: 268px; height: 360px; background: linear-gradient(180deg, #d8d6d2 0%, #cfc7bc 45%, #d9c2b0 65%, #e6e3df 100%); }
  .photo-footings-b { left: 896px; top: 348px; width: 264px; height: 360px; background: linear-gradient(180deg, #d8d6d2 0%, #cfc7bc 45%, #d9c2b0 65%, #e6e3df 100%); }

  .band { position: absolute; left: 0; top: 0; width: 1200px; height: 851px; }
  .band polygon { fill: var(--band); }

  .offer-badge { position: absolute; left: 80px; top: 718px; width: 130px; height: 133px; background: var(--offer-red); color: #fff; text-align: center; }
  .offer-title { font-family: "Oswald", Impact, sans-serif; font-size: 30px; line-height: 1; margin-top: 14px; letter-spacing: 0.5px; }
  .offer-stamp { display: inline-block; margin-top: 10px; border: 3px solid #fff; border-radius: 6px; padding: 2px 8px; font-family: "Oswald", Impact, sans-serif; font-size: 22px; line-height: 0.95; transform: rotate(-14deg); }

  .contact { position: absolute; left: 240px; width: 720px; top: 724px; text-align: center; color: var(--navy); font-style: normal; font-size: 19.5px; font-weight: 500; line-height: 22px; }
  .contact-org { font-size: 20px; letter-spacing: 0.3px; }
  .contact .label { color: var(--label-red); }
</style>
</head>
<body>
  <main class="flyer">
    <header class="brand">
      <p class="brand-name">Bramlow Building</p>
    </header>

    <section class="intro">
      <p class="intro-lead">We specialise in;</p>
      <p class="intro-services">General building,<br>building extensions,<br>loft conversions,<br>basement<br>conversions, and<br>general property<br>refurbishment with<br>30yrs experience<br>within the industry</p>
    </section>

    <p class="strapline">On time –<br>On budget –<br>guaranteed</p>

    <div class="photo photo-apartments" role="img" aria-label="Photo of a completed brick apartment building with large windows"></div>
    <div class="photo photo-house" role="img" aria-label="Photo of a refurbished detached house with oak porch and garden steps"></div>
    <div class="photo photo-floor" role="img" aria-label="Photo of insulation boards laid over a new floor slab"></div>
    <div class="photo photo-footings-a" role="img" aria-label="Photo of builders laying blockwork footings for an extension"></div>
    <div class="photo photo-footings-b" role="img" aria-label="Photo of builders laying blockwork footings for an extension"></div>

    <svg class="band" viewBox="0 0 1200 851" aria-hidden="true">
      <polygon points="0,612 552,702 597,660 643,702 1200,612 1200,851 0,851"/>
    </svg>

    <div class="offer-badge">
      <div class="offer-title">OFFER!</div>
      <div class="offer-stamp">VAT<br>FREE</div>
    </div>

    <address class="contact">
      <div class="contact-org">GUILD OF TRUSTED BUILDERS</div>
      <div>Halden House, 22/24 Marlow Street, London EC2A 4PQ.</div>
      <div><span class="label">Tel:</span> 020 7946 0183 <span class="label">Fax:</span> 020 7946 0522 <span class="label">email:</span> office@trustedbuilders.co.uk</div>
      <div>Website: www.trustedbuilders.co.uk.</div>
    </address>
  </main>
</body>
</html>
```